Hero Image for Homepage Header

I need an hero image (main image) for a new web site.
The site will be a sales consultancy/coaching business aimed at B2B software sales professionals and software/SaaS firms. The aim of the business is to help sales professionals and tech firms transform their sales performance and close more deals.

The two styles of hero images I like can be seen here:
- Plinkora.com
- Vextrino.com

You can come up with a concept that is like one of these.

Basically the image should show a familiar UI screen of a sales professional's CRM dashboard (see attachments).
In the animated gif (which I hate - it's poor quality) you can see how the data points all improve. This represents the sales 'transformation'.

I'd like you to re-create a UI screen from quortalim.com (the attachments, Quortalim1 and Quortalim2 are taken from the Quortalim CRM software. I want you to recreate them from scratch but in a more high-quality manner and come up with a hero image design concept that will show how poor results on screen can become better.
The attachment Quortalim2 shows how the results from Quortalim1 have been improved.

If you think an animated gif would be better, that's fine.

I'd like your design concept to include the following points (in freehand text style just like in the Plinkora.com image)

- 4x pipeline
- Higher conversions
- More deals CLOSED-WON

Come up with something stunning

```html
<!DOCTYPE html>
<html lang="en">
<head>
<meta charset="utf-8">
<title>Sales Transformation Hero</title>
<link rel="stylesheet" href="https://fonts.googleapis.com/css2?family=Questrial&family=Carlito&family=Gochi+Hand&family=Roboto:wght@400;500;700&display=swap">
<style>
:root{
  --ink:#3a3a3a;
  --navy:#053a6a;
  --headline-blue:#0b3a66;
  --sky:#c5dceb;
  --paper:#ffffff;
  --grey-bar:#d9d9d9;
  --line:#e3e3e3;
  --muted:#7a7a7a;
  --teal-text:#0f6e5e;
  --f1:#1aa3e8; --f2:#1a2f5a; --f3:#72dcd6; --f4:#12a99b; --f5:#e8c96b; --f6:#f0a210;
  --g-red:#f06b6b; --g-yellow:#f5cf47; --g-green:#3dd39a;
}
*{margin:0;padding:0;box-sizing:border-box}
html,body{width:1200px;height:675px;overflow:hidden;background:#fff}
.hero{position:relative;width:1200px;height:675px;overflow:hidden;background:var(--paper);font-family:"Roboto",sans-serif}
.backdrop{position:absolute;left:568px;top:-157px;width:988px;height:988px;border-radius:50%;background:var(--sky)}
.brand{position:absolute;left:56px;top:21px;display:flex;align-items:center;gap:7px}
.brand-box{width:64px;height:28px;background:var(--grey-bar)}
.brand-name{font-family:"Questrial",sans-serif;font-size:14px;letter-spacing:3px;color:#111}
.headline{position:absolute;left:64px;top:198px;font-family:"Questrial",sans-serif;font-weight:400;font-size:46px;line-height:53px;color:var(--ink);letter-spacing:-1.5px}
.headline .accent{display:block;color:var(--headline-blue);padding-left:10px}
.intro{position:absolute;left:64px;top:380px;width:480px;font-family:"Carlito",sans-serif;font-size:13.4px;line-height:17px;color:#333}
.actions{position:absolute;left:64px;top:489px;display:flex;gap:14px}
.btn{width:172px;height:49px;display:flex;align-items:center;justify-content:center;font-family:"Carlito",sans-serif;font-size:17px;letter-spacing:.5px}
.btn-primary{background:var(--navy);color:#fff}
.btn-outline{border:2px solid var(--navy);color:var(--navy);background:#fff}

.card{position:absolute;background:#fff;box-shadow:0 1px 4px rgba(0,0,0,.18)}
.note{position:absolute;background:#fff;font-family:"Gochi Hand",cursive;color:var(--headline-blue);line-height:1.05;text-align:center;display:flex;flex-direction:column;justify-content:center}
.arrows{position:absolute;left:0;top:0;width:1200px;height:675px;pointer-events:none}

.pipeline-head{left:783px;top:125px;width:197px;height:51px;padding:14px 15px 0}
.card-title{font-family:"Roboto",sans-serif;font-weight:500;font-size:13.5px;letter-spacing:.5px;color:#222}
.card-sub{font-size:9.5px;color:var(--muted);margin-top:5px}
.info{position:absolute;right:12px;top:16px;width:13px;height:13px;border-radius:50%;border:1px solid #777;font-size:8px;line-height:11px;text-align:center;color:#555}
.pipeline-body{left:783px;top:181px;width:197px;height:152px}
.chart-label{position:absolute;font-size:6px;font-weight:700;color:#111}
.legend{position:absolute;list-style:none;font-size:5.6px;color:#222;text-align:right}
.legend li{display:flex;justify-content:flex-end;align-items:center;gap:9px}
.legend i{display:block;width:7px;height:7px}

.arr-card{left:995px;top:227px;width:189px;height:192px}
.arr-card .head{padding:16px 15px 0;height:49px;border-bottom:1px solid #ccc}

.dashboard{left:691px;top:375px;width:464px;height:247px;box-shadow:none}
.dash-bar{position:absolute;left:3px;top:2px;width:300px;height:19px;background:var(--grey-bar);display:flex;align-items:center;gap:6px;padding-left:4px}
.dash-bar .mark{width:9px;height:9px;background:#e0524a;border-radius:2px}
.dash-bar p{font-size:5.2px;line-height:5px;color:#444}
.tile{position:absolute;border:1px solid var(--line);border-radius:6px;background:#fff;padding:4px 10px}
.tile h4{font-size:5.8px;font-weight:500;color:#333}
.tile h5{font-size:5.6px;font-weight:400;color:#666}
.big-figure{font-size:30px;color:var(--teal-text);text-align:center;margin-top:22px}
.top-table{width:100%;border-collapse:collapse;margin-top:6px;font-size:3.2px}
.top-table th{background:#f1f1f1;text-align:left;font-weight:400;padding:2px 3px;font-size:3.4px}
.top-table td{border-bottom:1px solid #eee;padding:.6px 3px;color:#333}
.top-table td:first-child{color:#1aa3e8}
</style>
</head>
<body>
<main class="hero">
  <div class="backdrop"></div>

  <div class="brand"><span class="brand-box"></span><span class="brand-name">LOGO</span></div>

  <h1 class="headline">LOREM IPSUM DOLOR<span class="accent">LOREM IPSUM</span>LOREM IPSUM DOLOR</h1>

  <p class="intro">Lorem ipsum dolor sit amet, consetetur sadipscing elitr, sed diam nonumy eirmod tempor invidunt ut labore et dolore magna aliquyam erat, sed diam voluptua. At vero eos et accusam et justo duo dolores et ea rebum. Stet clita kasd gubergren, no sea takimata sanctus est Lorem ipsum dolor sit amet. Lorem ipsum dolor sit amet, consetetur sadipscing elitr, sed diam no</p>

  <div class="actions">
    <a class="btn btn-primary">TRY FOR FREE</a>
    <a class="btn btn-outline">GET INFO</a>
  </div>

  <!-- Sales dashboard -->
  <section class="card dashboard">
    <div class="dash-bar"><span class="mark"></span><p>Dashboard<br>Sales<br><span style="color:#888">September 2021</span></p></div>

    <div class="tile" style="left:4px;top:33px;width:137px;height:88px">
      <h4>MTD Total ARR</h4><h5>MTD Closed Won Opportunities</h5>
      <svg viewBox="0 0 200 135" width="104" height="70" style="display:block;margin:2px auto 0">
        <path d="M24.8 127.4A80 80 0 0 1 43.4 43.4" fill="none" stroke="var(--g-red)" stroke-width="9" stroke-linecap="round"/>
        <path d="M43.4 43.4A80 80 0 0 1 151.4 38.7" fill="none" stroke="var(--g-yellow)" stroke-width="9"/>
        <path d="M151.4 38.7A80 80 0 0 1 175.2 127.4" fill="none" stroke="var(--g-green)" stroke-width="9" stroke-linecap="round"/>
        <polygon points="56,74 112,101 108,107" fill="var(--f2)"/>
        <text x="115" y="112" font-size="17" fill="var(--teal-text)" text-anchor="middle" font-weight="500">$ 726 K</text>
        <text x="115" y="130" font-size="13" fill="#666" text-anchor="middle">47%</text>
      </svg>
    </div>

    <div class="tile" style="left:156px;top:33px;width:161px;height:88px">
      <h4>MTD Your Pipeline Opportunities</h4>
      <span class="chart-label" style="left:37px;top:18px;font-size:4.5px">Sum of Amount</span>
      <svg viewBox="0 0 100 150" width="41" height="60" style="position:absolute;left:37px;top:25px">
        <g font-size="9" fill="#fff" text-anchor="middle" font-family="Roboto,sans-serif">
        <polygon points="0,0 100,0 96,25 4,25" fill="var(--f1)"/><text x="50" y="16">$ 28 K</text>
        <polygon points="4,25 96,25 92,50 8,50" fill="var(--f2)"/><text x="50" y="41">$ 56 K</text>
        <polygon points="8,50 92,50 88,75 12,75" fill="var(--f3)"/><text x="50" y="66">$ 35 K</text>
        <polygon points="12,75 88,75 84,100 16,100" fill="var(--f4)"/><text x="50" y="91">$ 101 K</text>
        <polygon points="16,100 84,100 80,125 20,125" fill="var(--f5)"/><text x="50" y="116">$ 158 K</text>
        <polygon points="20,125 80,125 76,150 24,150" fill="var(--f6)"/><text x="50" y="141">$ 349 K</text>
        </g>
      </svg>
      <ul class="legend" style="right:14px;top:25px;font-size:4.4px;line-height:7.5px">
        <li style="font-weight:700">Stege</li>
        <li>Initial Contact<i style="background:var(--f1);width:4px;height:4px"></i></li>
        <li>Discovery Call<i style="background:var(--f2);width:4px;height:4px"></i></li>
        <li>Demo Delivered<i style="background:var(--f3);width:4px;height:4px"></i></li>
        <li>Technical Validation<i style="background:var(--f4);width:4px;height:4px"></i></li>
        <li>Proposal<i style="background:var(--f5);width:4px;height:4px"></i></li>
        <li>Negotiation<i style="background:var(--f6);width:4px;height:4px"></i></li>
      </ul>
    </div>

    <div class="tile" style="left:321px;top:33px;width:139px;height:88px;border-top:none;border-radius:0 0 6px 6px">
      <h5 style="margin-top:2px">FYTD Closed Won Opportunities</h5>
      <div class="big-figure">$1.1 M</div>
    </div>

    <div class="tile" style="left:4px;top:129px;width:137px;height:88px">
      <h4>FYTD Total ARR</h4><h5>FYTD Closed Won Opportunities</h5>
      <svg viewBox="0 0 200 135" width="104" height="70" style="display:block;margin:2px auto 0">
        <path d="M24.8 127.4A80 80 0 0 1 43.4 43.4" fill="none" stroke="var(--g-red)" stroke-width="9" stroke-linecap="round"/>
        <path d="M43.4 43.4A80 80 0 0 1 151.4 38.7" fill="none" stroke="var(--g-yellow)" stroke-width="9"/>
        <path d="M151.4 38.7A80 80 0 0 1 175.2 127.4" fill="none" stroke="var(--g-green)" stroke-width="9" stroke-linecap="round"/>
        <polygon points="58,70 112,95 108,101" fill="var(--f2)"/>
        <text x="115" y="112" font-size="17" fill="var(--teal-text)" text-anchor="middle" font-weight="500">$ 21 K</text>
        <text x="115" y="130" font-size="13" fill="#666" text-anchor="middle">16%</text>
      </svg>
    </div>

    <div class="tile" style="left:154px;top:129px;width:163px;height:88px">
      <h4>FYTD Your Pipeline Opportunities</h4>
      <span class="chart-label" style="left:41px;top:15px;font-size:5px">Sum of Amount</span>
      <svg viewBox="0 0 100 150" width="41" height="60" style="position:absolute;left:39px;top:22px">
        <g font-size="9" fill="#fff" text-anchor="middle" font-family="Roboto,sans-serif">
        <polygon points="0,0 100,0 96,25 4,25" fill="var(--f1)"/><text x="50" y="16">$ 119 K</text>
        <polygon points="4,25 96,25 92,50 8,50" fill="var(--f2)"/><text x="50" y="41">$ 118 K</text>
        <polygon points="8,50 92,50 88,75 12,75" fill="var(--f3)"/><text x="50" y="66">$ 228 K</text>
        <polygon points="12,75 88,75 84,100 16,100" fill="var(--f4)"/><text x="50" y="91">$ 255 K</text>
        <polygon points="16,100 84,100 80,125 20,125" fill="var(--f5)"/><text x="50" y="116">$ 204 K</text>
        <polygon points="20,125 80,125 76,150 24,150" fill="var(--f6)"/><text x="50" y="141">$ 88 K</text>
        </g>
      </svg>
      <ul class="legend" style="right:14px;top:22px;font-size:4.4px;line-height:7.5px">
        <li style="font-weight:700">Stege</li>
        <li>Initial Contact<i style="background:var(--f1);width:4px;height:4px"></i></li>
        <li>Discovery Call<i style="background:var(--f2);width:4px;height:4px"></i></li>
        <li>Demo Delivered<i style="background:var(--f3);width:4px;height:4px"></i></li>
        <li>Technical Validation<i style="background:var(--f4);width:4px;height:4px"></i></li>
        <li>Proposal<i style="background:var(--f5);width:4px;height:4px"></i></li>
        <li>Negotiation<i style="background:var(--f6);width:4px;height:4px"></i></li>
      </ul>
    </div>

    <div class="tile" style="left:321px;top:129px;width:139px;height:88px">
      <h4>Your 10 Opportunities</h4><h5>FYTD Top 10 FYTD Opportunities</h5>
      <table class="top-table">
        <tr><th>Opportunity Name</th><th></th><th>ARR</th></tr>
        <tr><td>Nevora</td><td>69K</td><td>828K</td></tr>
        <tr><td>Ostrel</td><td>53K</td><td>636K</td></tr>
        <tr><td>Brenlock Capital</td><td>46K</td><td>552K</td></tr>
        <tr><td>Quindle</td><td>38K</td><td>456K</td></tr>
        <tr><td>Harvane Bank</td><td>33K</td><td>396K</td></tr>
        <tr><td>Talmeri Group</td><td>28K</td><td>336K</td></tr>
        <tr><td>Corvix Telecom</td><td>28K</td><td>336K</td></tr>
        <tr><td>Eastbrook Health</td><td>23K</td><td>252K</td></tr>
        <tr><td>Velmora</td><td>18K</td><td>228K</td></tr>
      </table>
    </div>
  </section>

  <!-- Pipeline card -->
  <section class="card pipeline-head">
    <h3 class="card-title">PIPELINE</h3>
    <p class="card-sub">September 2021</p>
    <span class="info">i</span>
  </section>
  <section class="card pipeline-body">
    <span class="chart-label" style="left:22px;top:8px">Sum of Amount</span>
    <svg viewBox="0 0 100 150" width="81" height="117" style="position:absolute;left:11px;top:20px">
      <g font-size="8" fill="#fff" text-anchor="middle" font-family="Roboto,sans-serif">
      <polygon points="0,0 100,0 96,25 4,25" fill="var(--f1)"/><text x="50" y="15.5">$ 28 K</text>
      <polygon points="4,25 96,25 92,50 8,50" fill="var(--f2)"/><text x="50" y="40.5">$ 56 K</text>
      <polygon points="8,50 92,50 88,75 12,75" fill="var(--f3)"/><text x="50" y="65.5">$ 35 K</text>
      <polygon points="12,75 88,75 84,100 16,100" fill="var(--f4)"/><text x="50" y="90.5">$ 101 K</text>
      <polygon points="16,100 84,100 80,125 20,125" fill="var(--f5)"/><text x="50" y="115.5">$ 158 K</text>
      <polygon points="20,125 80,125 76,150 24,150" fill="var(--f6)"/><text x="50" y="140.5">$ 349 K</text>
      </g>
    </svg>
    <ul class="legend" style="right:16px;top:20px;line-height:14.8px">
      <li style="font-weight:700">Stege</li>
      <li>Initial Contact<i style="background:var(--f1)"></i></li>
      <li>Discovery Call<i style="background:var(--f2)"></i></li>
      <li>Demo Delivered<i style="background:var(--f3)"></i></li>
      <li>Technical Validation<i style="background:var(--f4)"></i></li>
      <li>Proposal<i style="background:var(--f5)"></i></li>
      <li>Negotiation<i style="background:var(--f6)"></i></li>
    </ul>
  </section>

  <!-- FYTD ARR card -->
  <section class="card arr-card">
    <div class="head">
      <h3 class="card-title">FYTD Total ARR</h3>
      <p class="card-sub" style="margin-top:6px">FYTD Closed Won Opportunities</p>
      <span class="info">i</span>
    </div>
    <svg viewBox="0 0 200 135" width="176" height="119" style="display:block;margin:12px auto 0">
      <path d="M24.8 127.4A80 80 0 0 1 43.4 43.4" fill="none" stroke="var(--g-red)" stroke-width="8" stroke-linecap="round"/>
      <path d="M43.4 43.4A80 80 0 0 1 151.4 38.7" fill="none" stroke="var(--g-yellow)" stroke-width="8"/>
      <path d="M151.4 38.7A80 80 0 0 1 175.2 127.4" fill="none" stroke="var(--g-green)" stroke-width="8" stroke-linecap="round"/>
      <g font-size="4" fill="#999" text-anchor="middle">
        <text x="36" y="118">$0</text><text x="40" y="86">$100K</text><text x="50" y="64">$200K</text>
        <text x="68" y="46">$400K</text><text x="88" y="37">$600K</text><text x="112" y="37">$800K</text>
        <text x="130" y="44">$1M</text><text x="146" y="58">$1.2M</text><text x="157" y="76">$1.3M</text>
        <text x="162" y="98">$1.4M</text><text x="163" y="120">$1.5M</text>
      </g>
      <polygon points="94,38 104,93 96,94" fill="var(--f2)"/>
      <text x="106" y="117" font-size="16" fill="var(--teal-text)" text-anchor="middle" font-weight="500">$ 726 K</text>
      <text x="106" y="133" font-size="12" fill="#666" text-anchor="middle">47%</text>
    </svg>
  </section>

  <!-- Handwritten notes -->
  <div class="note" style="left:741px;top:83px;width:121px;height:31px;font-size:21px">4x pipeline</div>
  <div class="note" style="left:1039px;top:109px;width:140px;height:47px;font-size:20px">Closed-won<br>More Deals</div>
  <div class="note" style="left:644px;top:284px;width:137px;height:47px;font-size:20px">Higher<br>conversions</div>

  <svg class="arrows" viewBox="0 0 1200 675" fill="none" stroke="var(--headline-blue)" stroke-width="4" stroke-linecap="round" stroke-linejoin="round">
    <path d="M822 70C850 45 900 48 915 75C922 88 926 105 927 122"/>
    <path d="M912 108L927 122L930 102"/>
    <path d="M1052 137C1026 150 1018 175 1027 198C1031 208 1036 215 1042 224"/>
    <path d="M1024 210L1042 224L1043 203"/>
    <path d="M780 304C806 299 826 315 826 340C826 352 824 362 822 372"/>
    <path d="M814 358L822 372L830 360"/>
  </svg>
</main>
</body>
</html>
```